Courses Report - Analytics Redesign

We are a Learning Management System company that is looking to redesign our reporting suite in our product. We would like to add more graphs and visualizations to our reporting help communicate results and give our reporting a more modern look. Screenshots include our current courses report so that you can see the filters and type of data that our users search for. We are using Varno Metrics as our reporting service and please see https://www.varnometrics-demo.net/visual-gallery/ for examples of what type of visualizations can be generated.

Target Market(s)

LMS Administrators, Marketing and Sales Product Trainers

Number of Pages Required

1 page

Font styles to use
Sans Serif

Colors
33b8a4
33a6d7
0392cd
00a990
85cae6
87cfc6
cadf82
abd036
9bcb3b

Requirements
Must have
• Clean and simple look. Use Raleway as font. Easy to use and intuitive filtering. Ability to add/remove filters to the output. Graphical display of results that can drill down.
Nice to have
• Better way of listing other reports in menu on left.
Should not have
• Complicated graphs that cannot be easily understood.

```html
<!DOCTYPE html>
<html lang="en">
<head>
<meta charset="utf-8">
<title>Courses Report</title>
<link href="https://fonts.googleapis.com/css2?family=Raleway:wght@400;500;600;700&display=swap" rel="stylesheet">
<style>
:root{
  --page:#f4f6f6;
  --surface:#ffffff;
  --ink:#3d4447;
  --ink-soft:#5a6265;
  --muted:#9aa3a6;
  --line:#d9dfe0;
  --teal:#33b8a4;
  --teal-deep:#00a990;
  --teal-soft:#87cfc6;
  --blue:#33a6d7;
  --blue-deep:#0392cd;
  --blue-soft:#85cae6;
  --green:#9bcb3b;
  --green-mid:#abd036;
  --green-soft:#cadf82;
  --chip:#e6f5f3;
  --chip-ink:#2f7f74;
  --table-head:#e3f3f1;
  --row-alt:#f3faf9;
  --btn-light:#c7d0d2;
}
*{box-sizing:border-box;margin:0;padding:0}
html,body{width:1200px;height:1166px;overflow:hidden}
body{position:relative;background:var(--page);font-family:"Raleway",sans-serif;color:var(--ink);font-size:10.5px}
.abs{position:absolute}
.topbar{left:0;top:0;width:1200px;height:56px;background:var(--surface);border-bottom:1px solid var(--line)}
.brand{left:50px;top:15px;display:flex;align-items:center;gap:7px;font-weight:700;font-size:15px;color:var(--ink)}
.brand-dot{width:26px;height:26px;border-radius:50%;background:var(--teal)}
.main-nav a,.sub-nav a{position:absolute;color:var(--ink-soft);text-decoration:none;white-space:nowrap}
.main-nav a{top:22px}
.main-nav a.current,.sub-nav a.current{color:var(--ink);font-weight:500}
.main-nav a.current::after{content:"";position:absolute;left:0;right:0;top:19px;height:2px;background:var(--teal)}
.account{left:1022px;top:14px;display:flex;align-items:center;gap:8px;color:var(--ink-soft)}
.avatar{width:28px;height:28px;border-radius:50%;background:var(--chip);display:flex;align-items:center;justify-content:center;font-size:13px;color:var(--chip-ink)}
.subbar{left:0;top:57px;width:1200px;height:56px;background:var(--surface)}
.sub-nav a{top:22px}
.sub-nav a.current::after{content:"";position:absolute;left:0;right:0;top:17px;height:2px;background:var(--teal)}
.page-title{left:50px;top:145px;font-size:19px;font-weight:400}
.panel{left:50px;top:187px;width:1100px;height:475px;background:var(--surface)}
.label{position:absolute;font-weight:500;color:var(--ink)}
.field{position:absolute;height:23px;border:1px solid var(--line);background:var(--surface);display:flex;align-items:center;gap:4px;padding:0 6px}
.chip{background:var(--chip);padding:2px 5px;display:flex;align-items:center;gap:6px;color:var(--chip-ink);white-space:nowrap}
.chip svg{width:7px;height:7px}
.select{justify-content:space-between;padding:0 8px;color:var(--ink-soft)}
.select svg{width:7px;height:5px}
.hint{position:absolute;color:var(--muted)}
.box{position:absolute;width:14px;height:14px;border:1px solid var(--line);background:var(--surface)}
.box.on{border-color:var(--teal)}
.box svg{position:absolute;left:2px;top:3px;width:9px;height:7px}
.opt{position:absolute;color:var(--ink-soft);white-space:nowrap}
.group{position:absolute;color:var(--muted)}
.btn{position:absolute;height:23px;display:flex;align-items:center;justify-content:center;color:#fff;font-weight:600}
.btn.save{background:var(--blue-deep)}
.btn.generate{background:var(--teal-deep)}
.btn.export{background:var(--blue)}
.btn.reset{background:var(--btn-light)}
.section-title{left:50px;top:702px;font-size:15px;font-weight:400}
.filter-btn{left:1064px;top:702px;width:86px;height:23px;border:1px solid var(--teal-soft);background:var(--surface);color:var(--teal-deep);display:flex;align-items:center;justify-content:center}
.chart-card{top:739px;width:350px;height:255px;background:var(--surface)}
.chart-card h3{position:absolute;left:19px;top:19px;font-size:9px;letter-spacing:1px;font-weight:600;color:var(--muted)}
.chart-card svg{position:absolute;left:0;top:0}
.chart-card text{font-family:"Raleway",sans-serif;font-size:9px;fill:var(--ink-soft)}
.chart-card a rect{cursor:pointer}
.chart-teal .strong{fill:var(--teal)}.chart-teal .soft{fill:var(--teal-soft)}
.chart-blue .strong{fill:var(--blue-deep)}.chart-blue .soft{fill:var(--blue-soft)}
.chart-green .strong{fill:var(--green)}.chart-green .soft{fill:var(--green-soft)}
.results-table{left:50px;top:1021px;width:1100px;border-collapse:collapse;table-layout:fixed}
.results-table th{height:30px;background:var(--table-head);text-align:left;font-weight:600;font-size:9px;color:var(--ink)}
.results-table td{height:37.7px;color:var(--ink-soft)}
.results-table tbody tr{background:var(--surface)}
.results-table tbody tr:nth-child(2){background:var(--row-alt)}
.status-done{color:var(--teal-deep)}
.cell-box{display:inline-block;width:14px;height:14px;border:1px solid var(--line);background:var(--surface);vertical-align:middle}
</style>
</head>
<body>

<header class="abs topbar">
  <div class="abs brand"><span class="brand-dot"></span>Learnwell Hub</div>
  <nav class="main-nav">
    <a style="left:343px">Home</a>
    <a style="left:406px">Users</a>
    <a class="current" style="left:467px">Reports</a>
    <a style="left:537px">Content</a>
    <a style="left:609px">Site</a>
  </nav>
  <div class="abs account"><span class="avatar">D</span>Dana Whitfield
    <svg width="7" height="5" viewBox="0 0 7 5"><path d="M1 1l2.5 2.5L6 1" fill="none" stroke="#777"/></svg>
  </div>
</header>

<div class="abs subbar">
  <nav class="sub-nav">
    <a style="left:50px">Saved Reports</a>
    <a style="left:152px">Users</a>
    <a class="current" style="left:212px">Courses</a>
    <a style="left:285px">Due Dates</a>
    <a style="left:367px">Classroom Enrollment</a>
    <a style="left:504px">Course Survey</a>
    <a style="left:606px">Satisfaction Survey</a>
    <a style="left:728px">Purchase History</a>
  </nav>
</div>

<h1 class="abs page-title">Courses</h1>

<section class="abs panel">
  <span class="label" style="left:19px;top:16px">Groups</span>
  <div class="field" style="left:19px;top:35px;width:267px">
    <span class="chip">Sales <svg viewBox="0 0 7 7"><path d="M1 1l5 5M6 1L1 6" stroke="#2f7f74"/></svg></span>
  </div>
  <span class="label" style="left:317px;top:16px">Course sets</span>
  <div class="field" style="left:317px;top:35px;width:367px">
    <span class="chip">Course Type Examples <svg viewBox="0 0 7 7"><path d="M1 1l5 5M6 1L1 6" stroke="#2f7f74"/></svg></span>
    <span class="chip">Linkvale Learning <svg viewBox="0 0 7 7"><path d="M1 1l5 5M6 1L1 6" stroke="#2f7f74"/></svg></span>
    <span class="chip">Sales Skills <svg viewBox="0 0 7 7"><path d="M1 1l5 5M6 1L1 6" stroke="#2f7f74"/></svg></span>
  </div>
  <span class="label" style="left:715px;top:16px">Courses</span>
  <div class="field" style="left:715px;top:35px;width:365px">
    <span class="chip">5 Management Mistakes Blocking Sales Reps from Selling <svg viewBox="0 0 7 7"><path d="M1 1l5 5M6 1L1 6" stroke="#2f7f74"/></svg></span>
  </div>

  <span class="label" style="left:19px;top:83px">Course status</span>
  <div class="field select" style="left:19px;top:101px;width:267px">Active courses<svg viewBox="0 0 7 5"><path d="M1 1l2.5 2.5L6 1" fill="none" stroke="#777"/></svg></div>
  <span class="label" style="left:317px;top:83px">User Status</span>
  <span class="hint" style="left:318px;top:108px">Training status</span>
  <div class="field select" style="left:396px;top:101px;width:96px">Complete<svg viewBox="0 0 7 5"><path d="M1 1l2.5 2.5L6 1" fill="none" stroke="#777"/></svg></div>
  <span class="hint" style="left:524px;top:108px">User status</span>
  <div class="field select" style="left:587px;top:101px;width:96px">Complete<svg viewBox="0 0 7 5"><path d="M1 1l2.5 2.5L6 1" fill="none" stroke="#777"/></svg></div>
  <span class="label" style="left:715px;top:83px">Date range (logged in on)</span>
  <div class="field select" style="left:715px;top:101px;width:96px">01/01/2019<svg viewBox="0 0 7 5"><path d="M1 1l2.5 2.5L6 1" fill="none" stroke="#777"/></svg></div>
  <div class="field select" style="left:824px;top:101px;width:96px">01/31/2019<svg viewBox="0 0 7 5"><path d="M1 1l2.5 2.5L6 1" fill="none" stroke="#777"/></svg></div>

  <span class="label" style="left:19px;top:148px">Report fields</span>
  <span class="box" style="left:19px;top:172px"></span><span class="opt" style="left:42px;top:173px">Select all</span>

  <span class="group" style="left:19px;top:206px">Users</span>
  <span class="box on" style="left:111px;top:206px"><svg viewBox="0 0 9 7"><path d="M1 3.5l2.5 2.5L8 1" fill="none" stroke="#00a990" stroke-width="1.3"/></svg></span><span class="opt" style="left:134px;top:206px">Users: first name</span>
  <span class="box on" style="left:348px;top:206px"><svg viewBox="0 0 9 7"><path d="M1 3.5l2.5 2.5L8 1" fill="none" stroke="#00a990" stroke-width="1.3"/></svg></span><span class="opt" style="left:372px;top:206px">Users: last name</span>
  <span class="box" style="left:586px;top:206px"></span><span class="opt" style="left:609px;top:206px">Users: email address</span>
  <span class="box" style="left:839px;top:206px"></span><span class="opt" style="left:862px;top:206px">Users: phone number</span>

  <span class="box" style="left:111px;top:246px"></span><span class="opt" style="left:134px;top:246px">Users: company number</span>
  <span class="box" style="left:348px;top:246px"></span><span class="opt" style="left:372px;top:246px">Users: company city</span>
  <span class="box" style="left:586px;top:246px"></span><span class="opt" style="left:609px;top:246px">Users: company state</span>
  <span class="box" style="left:839px;top:246px"></span><span class="opt" style="left:862px;top:246px">Users: company zip</span>

  <span class="group" style="left:19px;top:286px">Courses</span>
  <span class="box on" style="left:111px;top:286px"><svg viewBox="0 0 9 7"><path d="M1 3.5l2.5 2.5L8 1" fill="none" stroke="#00a990" stroke-width="1.3"/></svg></span><span class="opt" style="left:134px;top:286px">Courses: user status</span>
  <span class="box on" style="left:348px;top:286px"><svg viewBox="0 0 9 7"><path d="M1 3.5l2.5 2.5L8 1" fill="none" stroke="#00a990" stroke-width="1.3"/></svg></span><span class="opt" style="left:372px;top:286px">Courses: completion date</span>
  <span class="box" style="left:586px;top:286px"></span><span class="opt" style="left:609px;top:286px">Courses: user score</span>
  <span class="box" style="left:839px;top:286px"></span><span class="opt" style="left:862px;top:286px">Courses: user session time</span>

  <span class="group" style="left:19px;top:326px">Custom</span>
  <span class="box" style="left:111px;top:326px"></span><span class="opt" style="left:134px;top:326px">Custom: position</span>
  <span class="box" style="left:348px;top:326px"></span><span class="opt" style="left:372px;top:326px">Custom: employee ID</span>
  <span class="box on" style="left:586px;top:326px"><svg viewBox="0 0 9 7"><path d="M1 3.5l2.5 2.5L8 1" fill="none" stroke="#00a990" stroke-width="1.3"/></svg></span><span class="opt" style="left:609px;top:326px">Custom: Job role</span>
  <span class="box" style="left:839px;top:326px"></span><span class="opt" style="left:862px;top:326px">Custom: department</span>

  <span class="box" style="left:111px;top:366px"></span><span class="opt" style="left:134px;top:366px">Custom: status</span>

  <span class="label" style="left:19px;top:414px">Report name</span>
  <div class="field" style="left:19px;top:433px;width:267px"></div>
  <span class="btn save" style="left:299px;top:433px;width:83px">Save report</span>
  <span class="btn reset" style="left:791px;top:433px;width:60px">Reset</span>
  <span class="btn generate" style="left:859px;top:433px;width:107px">Generate report</span>
  <span class="btn export" style="left:974px;top:433px;width:106px">Export to Excel</span>
</section>

<h2 class="abs section-title">Results</h2>
<span class="abs filter-btn">Filter results</span>

<div class="abs chart-card chart-teal" style="left:50px">
  <h3>TOP SALES REPS</h3>
  <svg width="350" height="255" viewBox="0 0 350 255">
    <g stroke="#e8eeee"><path d="M94 58H325M94 94H325M94 129H325M94 164H325M94 198H325M94 234H325"/></g>
    <path d="M94 46V234" stroke="#c3cbcc"/>
    <g text-anchor="end"><text x="82" y="79">Jon Harlow</text><text x="82" y="114">Evan Marsh</text><text x="82" y="149">Mila Brennan</text><text x="82" y="184">Lena Doyle</text><text x="82" y="219">Petra Hale</text></g>
    <a href="#rep-1"><rect class="strong" x="106" y="70" width="167" height="11"/></a><a href="#rep-2"><rect class="soft" x="106" y="105" width="135" height="11"/></a><a href="#rep-3"><rect class="strong" x="106" y="140" width="128" height="11"/></a><a href="#rep-4"><rect class="soft" x="106" y="175" width="91" height="11"/></a><a href="#rep-5"><rect class="strong" x="106" y="210" width="42" height="11"/></a>
  </svg>
</div>
<div class="abs chart-card chart-blue" style="left:425px">
  <h3>TOP SALES REPS</h3>
  <svg width="350" height="255" viewBox="0 0 350 255">
    <g stroke="#e8eeee"><path d="M94 58H325M94 94H325M94 129H325M94 164H325M94 198H325M94 234H325"/></g>
    <path d="M94 46V234" stroke="#c3cbcc"/>
    <g text-anchor="end"><text x="82" y="79">Jon Harlow</text><text x="82" y="114">Evan Marsh</text><text x="82" y="149">Mila Brennan</text><text x="82" y="184">Lena Doyle</text><text x="82" y="219">Petra Hale</text></g>
    <a href="#rep-1"><rect class="strong" x="106" y="70" width="167" height="11"/></a><a href="#rep-2"><rect class="soft" x="106" y="105" width="135" height="11"/></a><a href="#rep-3"><rect class="strong" x="106" y="140" width="128" height="11"/></a><a href="#rep-4"><rect class="soft" x="106" y="175" width="91" height="11"/></a><a href="#rep-5"><rect class="strong" x="106" y="210" width="42" height="11"/></a>
  </svg>
</div>
<div class="abs chart-card chart-green" style="left:800px">
  <h3>TOP SALES REPS</h3>
  <svg width="350" height="255" viewBox="0 0 350 255">
    <g stroke="#e8eeee"><path d="M94 58H325M94 94H325M94 129H325M94 164H325M94 198H325M94 234H325"/></g>
    <path d="M94 46V234" stroke="#c3cbcc"/>
    <g text-anchor="end"><text x="82" y="79">Jon Harlow</text><text x="82" y="114">Evan Marsh</text><text x="82" y="149">Mila Brennan</text><text x="82" y="184">Lena Doyle</text><text x="82" y="219">Petra Hale</text></g>
    <a href="#rep-1"><rect class="strong" x="106" y="70" width="167" height="11"/></a><a href="#rep-2"><rect class="soft" x="106" y="105" width="135" height="11"/></a><a href="#rep-3"><rect class="strong" x="106" y="140" width="128" height="11"/></a><a href="#rep-4"><rect class="soft" x="106" y="175" width="91" height="11"/></a><a href="#rep-5"><rect class="strong" x="106" y="210" width="42" height="11"/></a>
  </svg>
</div>

<table class="abs results-table">
  <colgroup><col style="width:59px"><col style="width:105px"><col style="width:117px"><col style="width:176px"><col style="width:304px"><col style="width:115px"><col style="width:117px"><col style="width:107px"></colgroup>
  <thead><tr><th style="padding-left:19px"><span class="cell-box"></span></th><th>First name</th><th>Last name</th><th>Email address</th><th>Course name</th><th>User status</th><th>Completion date</th><th>Job role</th></tr></thead>
  <tbody>
    <tr id="rep-0"><td style="padding-left:19px"><span class="cell-box"></span></td><td>Victor</td><td>Moreno</td><td>victorm@brightlane.com</td><td>Determining Customer Needs</td><td class="status-done">Completed</td><td>04/21/2016</td><td>Manager</td></tr>
    <tr id="rep-1"><td style="padding-left:19px"><span class="cell-box"></span></td><td>Jon</td><td>Harlow</td><td>jon.harlow@mailbox.com</td><td>5 Management Mistakes Blocking Sales Reps from Selling</td><td class="status-done">Completed</td><td>01/17/2019</td><td>Sales rep</td></tr>
    <tr id="rep-5"><td style="padding-left:19px"><span class="cell-box"></span></td><td>Petra</td><td>Hale</td><td>petra.hale@inboxly.com</td><td>PDF -- The LMS Evaluation Checklist</td><td class="status-done">Completed</td><td>04/21/2016</td><td>Manager</td></tr>
  </tbody>
</table>

</body>
</html>
```